New Business Card Design Project

I'd like a business card design around the same modern style that I used on my website www.brovanhs.com
It's gonna be one of those round corners double-sided business cards with maybe a big logo on the front and all the info on the back of the card.

Contact Information for Business Card

Marco Delgado
425-317-6084
www.brovanhs.com

www.facebook.com/BrovanHomeServices
www.intsgram.com/BrovanHomeServices

Requirements
Must have
• it needs to look elegant and modern

```html
<!DOCTYPE html>
<html lang="en">
<head>
<meta charset="utf-8">
<title>Brovan Home Services – Business Card</title>
<link href="https://fonts.googleapis.com/css2?family=Work+Sans:wght@400;500;700&display=swap" rel="stylesheet">
<style>
  :root {
    --bg: #e9e7e4;
    --card-dark: #111214;
    --card-light: #ffffff;
    --brand-blue: #1e8fe0;
    --ink: #222326;
    --ink-soft: #55575c;
    --band-dark: #232427;
  }
  * { box-sizing: border-box; margin: 0; padding: 0; }
  html, body {
    width: 1200px; height: 715px; overflow: hidden;
    background: var(--bg);
    font-family: "Work Sans", sans-serif;
  }
  .canvas {
    position: relative; width: 1200px; height: 715px;
    display: flex; align-items: center; justify-content: center; gap: 40px;
  }
  .card {
    position: relative; width: 540px; height: 309px;
    border-radius: 8px; overflow: hidden;
    box-shadow: 0 10px 28px rgba(0,0,0,.18);
  }

  /* Front */
  .card-front {
    background: var(--card-dark);
    display: flex; align-items: center; justify-content: center;
  }
  .wordmark {
    display: flex; align-items: center; gap: 14px;
    color: var(--brand-blue);
    font-weight: 700;
    white-space: nowrap;
  }
  .wordmark-dot {
    width: 18px; height: 18px; border-radius: 50%;
    background: var(--brand-blue);
    flex: none;
  }
  .card-front .wordmark { font-size: 38px; letter-spacing: -.5px; }

  /* Back */
  .card-back { background: var(--card-light); color: var(--ink); }
  .name-block {
    position: absolute; left: 0; top: 34px;
    padding-left: 30px;
  }
  .name-block::before {
    content: ""; position: absolute; left: 0; top: 2px;
    width: 9px; height: 30px; background: var(--brand-blue);
  }
  .person-name {
    color: var(--brand-blue); font-size: 25px; font-weight: 500;
    letter-spacing: .5px; text-transform: uppercase; line-height: 1;
  }
  .person-role { font-size: 14px; color: var(--ink-soft); margin-top: 3px; }

  .contact-list {
    position: absolute; left: 30px; top: 108px;
    list-style: none; font-size: 13.5px; line-height: 19px; color: var(--ink);
  }
  .contact-list li { display: flex; align-items: center; gap: 8px; }
  .contact-icon { width: 10px; height: 10px; flex: none; }

  .card-back .wordmark {
    position: absolute; right: 28px; top: 90px;
    font-size: 24px; gap: 10px;
  }
  .card-back .wordmark-dot { width: 12px; height: 12px; }

  .divider {
    position: absolute; left: 250px; right: 26px; top: 150px;
    height: 1.5px; background: var(--brand-blue);
  }

  .address {
    position: absolute; right: 28px; bottom: 34px;
    text-align: right; font-size: 14px; line-height: 19px; color: var(--ink);
    font-style: normal;
  }
  .footer-band {
    position: absolute; left: 0; right: 0; bottom: 0; height: 12px;
    display: flex;
  }
  .footer-band .band-blue { width: 52%; background: var(--brand-blue); }
  .footer-band .band-dark { flex: 1; background: var(--band-dark); }
</style>
</head>
<body>
<main class="canvas">

  <section class="card card-front" aria-label="Card front">
    <div class="wordmark">
      <span class="wordmark-dot"></span>
      <span class="wordmark-text">Brovan Home Services</span>
    </div>
  </section>

  <section class="card card-back" aria-label="Card back">
    <div class="name-block">
      <p class="person-name">Marco Delgado</p>
      <p class="person-role">Director</p>
    </div>

    <ul class="contact-list">
      <li>
        <svg class="contact-icon" viewBox="0 0 10 10"><path d="M2 1 L4 1 L4.6 3 L3.5 3.8 Q4.5 5.8 6.2 6.5 L7 5.4 L9 6 L9 8 Q9 9 8 9 Q2 8.5 1 2 Q1 1 2 1 Z" fill="var(--brand-blue)"/></svg>
        425-317-6084
      </li>
      <li>
        <svg class="contact-icon" viewBox="0 0 10 10"><rect x="1" y="2" width="8" height="6" fill="none" stroke="var(--brand-blue)" stroke-width="1.2"/><path d="M1 2 L5 5.5 L9 2" fill="none" stroke="var(--brand-blue)" stroke-width="1.2"/></svg>
        info@brovanhs.com
      </li>
      <li>
        <svg class="contact-icon" viewBox="0 0 10 10"><circle cx="5" cy="5" r="4" fill="none" stroke="var(--brand-blue)" stroke-width="1.1"/><ellipse cx="5" cy="5" rx="1.8" ry="4" fill="none" stroke="var(--brand-blue)" stroke-width=".9"/><line x1="1" y1="5" x2="9" y2="5" stroke="var(--brand-blue)" stroke-width=".9"/></svg>
        www.brovanhs.com
      </li>
      <li>
        <svg class="contact-icon" viewBox="0 0 10 10"><rect x="1" y="1" width="8" height="8" rx="1.5" fill="var(--brand-blue)"/></svg>
        /BrovanHomeServices
      </li>
      <li>
        <svg class="contact-icon" viewBox="0 0 10 10"><circle cx="5" cy="5" r="4" fill="var(--brand-blue)"/></svg>
        /BrovanHomeServices
      </li>
    </ul>

    <div class="wordmark">
      <span class="wordmark-dot"></span>
      <span class="wordmark-text">Brovan Home Services</span>
    </div>

    <div class="divider"></div>

    <address class="address">
      2417 Marlow Ridge Road<br>
      Tulsa, OK 74105
    </address>

    <div class="footer-band">
      <span class="band-blue"></span>
      <span class="band-dark"></span>
    </div>
  </section>

</main>
</body>
</html>
```